New Carpathian Table Billboard

Need to prepare a billboard for a KOSHER supermarket that is under new ownership. The billboard needs to have a good catch phrase such as:

A NEW Fresh KOSHER Grocery Experience Has Arrived!

The Legacy Continues...
Stop In To See The NEW Carpathian Table Foods!

Kosher Grocery Shopping at it's Finest!
Come See The NEW & IMPROVED Carpathian Table Foods

No Pictures. Choose various color backgrounds and send me proofs. Think of other catchy phrases and provide examples. Don't only use the phrases I gave above.

The store was taken under new ownership and we want to promote the NEW and Improved Store.

Target Market(s)

Orthodox Jewish

Industry/Entity Type

Grocery Store

Requirements
Must have
• Logo
• Linwell & Harbury in Skokie
Nice to have
• No Pictures.
Should not have
• Too much wording.

```html
<!DOCTYPE html>
<html lang="en">
<head>
<meta charset="utf-8">
<title>Carpathian Table Foods – Billboard</title>
<link rel="stylesheet" href="https://fonts.googleapis.com/css2?family=Montserrat:wght@800;900&display=swap">
<style>
  :root {
    --navy: #0f1d3d;
    --white: #ffffff;
    --red: #e3262b;
    --yellow: #f2ea1d;
    --page: #f4f4f4;
  }
  * { margin: 0; padding: 0; box-sizing: border-box; }
  html, body {
    width: 1200px;
    height: 960px;
    overflow: hidden;
    background: var(--page);
  }
  .billboard {
    position: absolute;
    left: 20px;
    top: 428px;
    width: 1160px;
    height: 103px;
    background: var(--navy);
    overflow: hidden;
    font-family: "Montserrat", Arial, sans-serif;
  }
  .billboard__swoosh {
    position: absolute;
    inset: 0;
    width: 1160px;
    height: 103px;
  }
  .brand {
    position: absolute;
    left: 14px;
    top: 0;
    height: 103px;
    display: flex;
    align-items: center;
    gap: 8px;
  }
  .brand__dot {
    width: 18px;
    height: 18px;
    border-radius: 50%;
    background: var(--red);
    flex: none;
  }
  .brand__name {
    color: var(--navy);
    font-weight: 800;
    font-size: 15px;
    line-height: 1.1;
    text-transform: uppercase;
  }
  .headline {
    position: absolute;
    left: 250px;
    width: 690px;
    top: 6px;
    text-align: center;
    color: var(--white);
    font-weight: 900;
  }
  .headline__main {
    display: block;
    font-size: 47px;
    line-height: 52px;
    letter-spacing: 0.5px;
  }
  .headline__accent { color: var(--yellow); }
  .headline__sub {
    display: block;
    font-size: 34px;
    line-height: 40px;
    font-weight: 800;
    letter-spacing: 0.3px;
  }
  .location {
    position: absolute;
    right: 22px;
    top: 0;
    height: 103px;
    width: 190px;
    display: flex;
    flex-direction: column;
    justify-content: center;
    align-items: center;
    text-align: center;
    color: var(--white);
    font-weight: 800;
    font-size: 19px;
    line-height: 1.25;
  }
  .location__town { color: var(--yellow); }
</style>
</head>
<body>
  <section class="billboard" aria-label="Carpathian Table Foods billboard">
    <svg class="billboard__swoosh" viewBox="0 0 1160 103" aria-hidden="true">
      <path d="M0 0 H150 Q185 50 205 103 H0 Z" fill="var(--white)"/>
      <path d="M172 0 H184 Q222 50 252 103 H238 Q206 50 172 0 Z" fill="var(--red)"/>
      <path d="M188 0 H193 Q231 50 262 103 H256 Q226 50 188 0 Z" fill="var(--white)"/>
    </svg>

    <div class="brand">
      <span class="brand__dot"></span>
      <span class="brand__name">Carpathian<br>Table Foods</span>
    </div>

    <h1 class="headline">
      <span class="headline__main">A NEW Fresh <span class="headline__accent">KOSHER</span></span>
      <span class="headline__sub">Grocery Experience Has Arrived!</span>
    </h1>

    <p class="location">
      <span>Linwell &amp; Harbury</span>
      <span class="location__town">in Skokie</span>
    </p>
  </section>
</body>
</html>
```